Pepper & Palm Business Card FUN & EXCITING

Here is the Information for the Card:
Jaswinder Bains (Ravi)
E: RaviBains@postlark.com
C: (480) 555-0147
www.PepperPalmLV.com

We don't want traditional Indian cliche, We a playful bold and fun business card.

Files: https://files.cloudvessel.net/share/folders/7TqRmXpZ2vKa9LwBn4YcHd3JsEf6UoGi?usp=share_link

https://files.cloudvessel.net/share/folders/4MzXaQ8rTw2YbNcVk6PsLe5GhJdR3FoU?usp=share_link

Target Market(s)

Las Vegas Local Restaurant

Industry/Entity Type

Indian Restaurant

Contact Information for Business Card

Name, Email, Cell Phone, Company Logo

```html
<!DOCTYPE html>
<html lang="en">
<head>
<meta charset="utf-8">
<title>Pepper &amp; Palm — Business Card</title>
<link rel="stylesheet" href="https://fonts.googleapis.com/css2?family=Poppins:wght@400;600;800&display=swap">
<style>
  :root {
    --stage: #2b2b2b;
    --card-pink: #e01a5c;
    --accent-yellow: #f5c518;
    --accent-teal: #17b08f;
    --ink-white: #ffffff;
    --divider: rgba(255, 255, 255, 0.22);
    --art-cream: #f3e6c4;
    --art-orange: #ee7a2a;
    --art-rose: #e8648a;
  }
  * { box-sizing: border-box; margin: 0; padding: 0; }
  html, body {
    width: 1093px;
    height: 1200px;
    overflow: hidden;
    background: var(--stage);
    font-family: "Poppins", sans-serif;
  }
  .canvas { position: relative; width: 1093px; height: 1200px; }

  .card {
    position: absolute;
    left: 265px;
    height: 356px;
    background: var(--card-pink);
    border-radius: 26px;
    overflow: hidden;
  }
  .card--front { top: 227px; width: 576px; }
  .card--back  { top: 621px; width: 581px; }

  .brand {
    position: absolute;
    display: flex;
    align-items: flex-end;
    gap: 10px;
  }
  .card--front .brand { left: 32px; top: 100px; }
  .card--back .brand  { left: 40px; top: 136px; }

  .brand__name {
    color: var(--ink-white);
    font-weight: 800;
    text-transform: uppercase;
    line-height: 0.98;
    letter-spacing: 0.5px;
    font-size: 50px;
  }
  .brand__mark {
    width: 16px;
    height: 16px;
    border-radius: 50%;
    background: var(--accent-yellow);
    margin-bottom: 9px;
    flex: none;
  }

  .divider {
    position: absolute;
    left: 288px;
    top: 75px;
    width: 1px;
    height: 208px;
    background: var(--divider);
  }

  .contact { position: absolute; left: 309px; top: 112px; }
  .contact__name {
    color: var(--accent-yellow);
    font-weight: 600;
    font-size: 18.5px;
    letter-spacing: 0.3px;
    text-transform: uppercase;
    margin-bottom: 30px;
  }
  .contact__list { list-style: none; }
  .contact__item {
    display: flex;
    align-items: center;
    gap: 7px;
    color: var(--ink-white);
    font-size: 17px;
    height: 26.5px;
  }
  .contact__icon { width: 19px; height: 19px; flex: none; }

  .mascot-art {
    position: absolute;
    left: 298px;
    top: 58px;
    width: 290px;
    height: 310px;
    border-radius: 120px 0 0 0;
    background: radial-gradient(ellipse at 55% 45%, var(--ink-white) 0%, var(--art-cream) 40%, var(--art-rose) 75%, var(--art-orange) 100%);
    opacity: 0.9;
  }
</style>
</head>
<body>
<main class="canvas">

  <section class="card card--front" aria-label="Business card front">
    <div class="brand">
      <div class="brand__name">Pepper<br>&amp; Palm</div>
      <span class="brand__mark" aria-hidden="true"></span>
    </div>
    <div class="divider"></div>
    <div class="contact">
      <p class="contact__name">Jaswinder Bains (Ravi)</p>
      <ul class="contact__list">
        <li class="contact__item">
          <svg class="contact__icon" viewBox="0 0 24 24" aria-hidden="true"><path fill="var(--accent-yellow)" d="M6.6 10.8a15.1 15.1 0 0 0 6.6 6.6l2.2-2.2a1 1 0 0 1 1-.25 11.4 11.4 0 0 0 3.6.57 1 1 0 0 1 1 1V20a1 1 0 0 1-1 1A17 17 0 0 1 3 4a1 1 0 0 1 1-1h3.5a1 1 0 0 1 1 1c0 1.25.2 2.45.57 3.57a1 1 0 0 1-.25 1z"/></svg>
          <span>(480) 555-0147</span>
        </li>
        <li class="contact__item">
          <svg class="contact__icon" viewBox="0 0 24 24" aria-hidden="true"><rect x="2" y="5" width="20" height="14" fill="var(--accent-yellow)"/><path d="M2 5l10 8 10-8" fill="none" stroke="var(--card-pink)" stroke-width="1.6"/></svg>
          <span>RaviBains@postlark.com</span>
        </li>
        <li class="contact__item">
          <svg class="contact__icon" viewBox="0 0 24 24" aria-hidden="true"><g fill="none" stroke="var(--accent-yellow)" stroke-width="1.8"><circle cx="12" cy="12" r="9.5"/><ellipse cx="12" cy="12" rx="4.2" ry="9.5"/><path d="M2.5 12h19M4 7h16M4 17h16"/></g></svg>
          <span>www.PepperPalmLV.com</span>
        </li>
      </ul>
    </div>
  </section>

  <section class="card card--back" aria-label="Business card back">
    <div class="brand">
      <div class="brand__name">Pepper &amp;<br>Palm</div>
    </div>
    <div class="mascot-art" role="img" aria-label="Cartoon curry bowl mascot pointing upward, walking beside a naan, with hearts and sparkles"></div>
  </section>

</main>
</body>
</html>
```